Business card design Needed for new logo / Construction business, home extensions and new builds

We need a business card design using our new logo files which i will attach to this project :)

We are a small construction business specialising in home extensions, new builds and property development. We are very ambitious and would appreciate professional and elegant designs for our new business card.

Very serious about using the services on MakerQuarry and recently acquired our new logo from here :)

Please get involved, i will feedback when i can as i am very busy but can respond daily, thanks

Target Market(s)

People that want to build onto their houses, new building developments or adding too their existing property

Industry/Entity Type

Construction

Contact Information for Business Card

Renwick Tolliver Construction, Lionel Ashby (Managing Director), Tel 07822254961, email - info@renwick-tolliver, www.renwick-tolliver.co.uk

Colors

Designer to choose colors to be used in the design.

Requirements
Must have
• I like a deep grey on the back please. A lot of you have provided black from and back, try mixing things up a little. The black looks cool 😎 Thanks

```html
<!DOCTYPE html>
<html lang="en">
<head>
<meta charset="utf-8">
<title>Renwick Tolliver Construction – Business Card</title>
<link href="https://fonts.googleapis.com/css2?family=Montserrat:wght@400;500;600;700&display=swap" rel="stylesheet">
<style>
  :root {
    --stage: #4b4c4f;
    --card-front: #0b0b0c;
    --card-back: #2a2b2e;
    --pattern-a: #0f0f10;
    --pattern-b: #19191b;
    --gold: #dba82b;
    --silver: #d9dadc;
    --text-light: #f0efec;
  }
  * { box-sizing: border-box; margin: 0; padding: 0; }
  html, body {
    width: 1200px; height: 689px; overflow: hidden;
    background: var(--stage);
    font-family: "Montserrat", Arial, sans-serif;
  }
  .canvas {
    position: relative; width: 1200px; height: 689px;
    display: flex; align-items: center; justify-content: center; gap: 50px;
  }
  .card {
    position: relative; width: 530px; height: 303px;
    border-radius: 18px; overflow: hidden;
    box-shadow: 0 18px 40px rgba(0,0,0,.45);
  }
  /* Front – black */
  .card--front { background: var(--card-front); }
  .front__pattern {
    position: absolute; inset: 0;
    background: radial-gradient(ellipse at 50% 50%, var(--pattern-b), var(--pattern-a) 75%);
  }
  .brand {
    position: absolute; inset: 0;
    display: flex; flex-direction: column; align-items: center; justify-content: center; gap: 16px;
  }
  .brand__mark { width: 46px; height: 46px; background: var(--gold); }
  .brand__name {
    font-weight: 600; font-size: 26px; letter-spacing: .08em;
    text-transform: uppercase; color: var(--silver); text-align: center; line-height: 1.25;
  }
  .brand__rule {
    width: 280px; height: 2px;
    background: linear-gradient(90deg, transparent, var(--gold) 20%, var(--gold) 80%, transparent);
  }
  /* Back – deep grey */
  .card--back { background: var(--card-back); }
  .card--back::after {
    content: ""; position: absolute; left: 30px; right: 30px; bottom: 0; height: 2px;
    background: linear-gradient(90deg, transparent, var(--gold) 30%, var(--gold));
  }
  .back__brand {
    position: absolute; top: 34px; left: 0; right: 0;
    display: flex; flex-direction: column; align-items: center; gap: 10px;
  }
  .back__brand .brand__mark { width: 30px; height: 30px; }
  .back__brand .brand__name { font-size: 17px; }
  .back__brand .brand__rule { width: 210px; }
  .address {
    position: absolute; top: 150px; left: 0; right: 0; text-align: center;
    font-size: 12.5px; color: var(--text-light); letter-spacing: .02em;
  }
  .details {
    position: absolute; top: 186px; left: 0; right: 0;
    display: flex; justify-content: center; align-items: center; gap: 22px;
  }
  .person { text-align: right; }
  .person__name {
    font-weight: 700; font-size: 19px; color: var(--gold); letter-spacing: .04em; text-transform: uppercase;
  }
  .person__role { font-size: 12.5px; color: var(--text-light); margin-top: 3px; }
  .divider { width: 1.5px; height: 64px; background: var(--gold); }
  .contact { list-style: none; display: flex; flex-direction: column; gap: 6px; }
  .contact__item {
    display: flex; align-items: center; gap: 8px;
    font-size: 12.5px; color: var(--text-light);
  }
  .contact__icon { width: 12px; height: 12px; flex: none; }
</style>
</head>
<body>
<main class="canvas">

  <section class="card card--front" aria-label="Card front">
    <div class="front__pattern" role="img" aria-label="Embossed repeating monogram pattern in deep black tones"></div>
    <div class="brand">
      <span class="brand__mark"></span>
      <h1 class="brand__name">Renwick Tolliver<br>Construction</h1>
      <span class="brand__rule"></span>
    </div>
  </section>

  <section class="card card--back" aria-label="Card back">
    <div class="back__brand">
      <span class="brand__mark"></span>
      <h2 class="brand__name">Renwick Tolliver Construction</h2>
      <span class="brand__rule"></span>
    </div>

    <p class="address">Your address, City State, Zip 1234</p>

    <div class="details">
      <div class="person">
        <p class="person__name">Lionel Ashby</p>
        <p class="person__role">Managing Director</p>
      </div>
      <span class="divider"></span>
      <ul class="contact">
        <li class="contact__item">
          <svg class="contact__icon" viewBox="0 0 24 24" aria-hidden="true"><path fill="#dba82b" d="M6.6 10.8a15.1 15.1 0 0 0 6.6 6.6l2.2-2.2c.3-.3.7-.4 1-.2 1.1.4 2.3.6 3.6.6.6 0 1 .4 1 1V20c0 .6-.4 1-1 1A17 17 0 0 1 3 4c0-.6.4-1 1-1h3.5c.6 0 1 .4 1 1 0 1.3.2 2.5.6 3.6.1.3 0 .7-.2 1z"/></svg>
          07822254961
        </li>
        <li class="contact__item">
          <svg class="contact__icon" viewBox="0 0 24 24" aria-hidden="true"><rect x="2" y="5" width="20" height="14" rx="2" fill="#dba82b"/><path d="M3 6l9 7 9-7" fill="none" stroke="#2a2b2e" stroke-width="2"/></svg>
          info@renwick-tolliver
        </li>
        <li class="contact__item">
          <svg class="contact__icon" viewBox="0 0 24 24" aria-hidden="true"><circle cx="12" cy="12" r="10" fill="#dba82b"/><path d="M2 12h20M12 2c3 3 3 17 0 20M12 2c-3 3-3 17 0 20" fill="none" stroke="#2a2b2e" stroke-width="1.5"/></svg>
          www.renwick-tolliver.co.uk
        </li>
      </ul>
    </div>
  </section>

</main>
</body>
</html>
```